Attractive door board for entrance beautysalon

Make an attractive design for a board that can be glued on the front door of a beauty salon. The salon location has no window in the front so I need something catchy and attractive. The door board contains a list of the services and the website: www.zaalmira.be, and the text "Enkel op afspraak, bel 0486391524"

Target Market(s)

woman between 16 and 99 years old

Industry/Entity Type

Beauty Salon

Font styles to use
Sans Serif

Requirements
Must have
• A very nice, attractive but sober design.
• It must have a classy Morvelle, Vasq, ... chique design.
• The logo must be on it (in attachment)
• There must be the following list in it:
• Gelaatsverzorging
• Wimperverlenging
• Wimperlifting
• Suikerontharing
• Permanente Make Up
• Airbrush Tanning
• Manicure - Pedicure - Nalkyn
• and then the website www.zaalmira.be, and the text "Enkel op afspraak, bel 0486391524"
Nice to have
• a catchy design,
• max. width can be 75 cm and max height 180 cm as it is a design for a board that will be glued on a door.
Should not have
• orchid flowers, buddha look a likes

```html
<!DOCTYPE html>
<html lang="nl">
<head>
<meta charset="utf-8">
<title>Zaal Mira – Deurbord</title>
<link rel="stylesheet" href="https://fonts.googleapis.com/css2?family=Josefin+Sans:wght@300&family=Oswald:wght@300;400;500&display=swap">
<style>
  :root {
    --violet: #7331fa;
    --ink: #000000;
    --paper: #ffffff;
    --shade: #1a1a1a;
    --eye-blue: #6f9fc4;
    --eye-warm: #e9b35d;
  }
  * { margin: 0; padding: 0; box-sizing: border-box; }
  html, body { width: 1200px; height: 2880px; overflow: hidden; background: var(--ink); }
  .board {
    position: relative;
    width: 1200px;
    height: 2880px;
    background: var(--ink);
    overflow: hidden;
    font-family: "Oswald", "Arial Narrow", sans-serif;
    color: var(--paper);
  }
  .crown { position: absolute; left: 0; top: 0; width: 1200px; height: 540px; }
  .brand-ring {
    position: absolute;
    left: 480px; top: 250px;
    width: 240px; height: 240px;
    border: 4px solid var(--paper);
    border-radius: 50%;
  }
  .brand-name {
    position: absolute;
    left: 0; right: 0; top: 598px;
    text-align: center;
    font-family: "Josefin Sans", "Helvetica Neue", sans-serif;
    font-weight: 300;
    font-size: 74px;
    letter-spacing: 34px;
    padding-left: 34px;
    line-height: 1;
  }
  .brand-tagline {
    position: absolute;
    left: 0; right: 0; top: 736px;
    text-align: center;
    font-family: "Josefin Sans", "Helvetica Neue", sans-serif;
    font-weight: 300;
    font-size: 24px;
    letter-spacing: 19px;
    padding-left: 19px;
    line-height: 1;
  }
  .services { list-style: none; }
  .service {
    position: absolute;
    left: 0;
    width: 1200px;
    height: 144px;
    background: var(--violet);
    box-shadow: 0 14px 0 var(--shade);
    display: flex;
    align-items: center;
    padding-left: 78px;
    font-weight: 500;
    font-size: 74px;
    letter-spacing: 2px;
    text-transform: uppercase;
    line-height: 1;
  }
  .service .dot { margin-right: 28px; }
  .service .sep { margin: 0 24px; }
  .appointment {
    position: absolute;
    left: 0; top: 2124px;
    width: 1200px; height: 528px;
    background: var(--paper);
  }
  .appointment-art {
    position: absolute;
    left: 0; top: 24px;
    width: 360px; height: 470px;
    background: linear-gradient(135deg, var(--eye-warm) 0%, var(--eye-blue) 45%, #a872c9 75%, #f3eaf7 100%);
    opacity: 0.75;
  }
  .appointment-text {
    position: absolute;
    left: 468px; top: 170px;
    color: var(--ink);
    text-transform: uppercase;
    line-height: 1;
  }
  .appointment-note { font-weight: 300; font-size: 78px; letter-spacing: 2px; }
  .appointment-call { font-weight: 500; font-size: 82px; letter-spacing: 3px; margin-top: 34px; }
  .website {
    position: absolute;
    left: 0; right: 0; top: 2690px;
    text-align: center;
    font-weight: 500;
    font-size: 82px;
    letter-spacing: 16px;
    padding-left: 16px;
    text-transform: uppercase;
    line-height: 1;
  }
</style>
</head>
<body>
<main class="board">
  <svg class="crown" viewBox="0 0 1200 540" aria-hidden="true">
    <rect x="0" y="0" width="1200" height="540" fill="var(--violet)"/>
    <path d="M0 528 L0 470 C0 180 250 0 600 0 C950 0 1200 180 1200 470 L1200 528 Z" fill="var(--ink)"/>
    <rect x="0" y="520" width="1200" height="20" fill="var(--ink)"/>
  </svg>

  <div class="brand-ring" aria-hidden="true"></div>
  <h1 class="brand-name">ZAAL MIRA</h1>
  <p class="brand-tagline">SCHOONHEIDSINSTITUUT</p>

  <ul class="services">
    <li class="service" style="top:876px"><span class="dot">•</span>Gelaatsverzorging</li>
    <li class="service" style="top:1046px"><span class="dot">•</span>Wimperverlenging</li>
    <li class="service" style="top:1216px"><span class="dot">•</span>Wimperlifting</li>
    <li class="service" style="top:1386px"><span class="dot">•</span>Suikerontharing</li>
    <li class="service" style="top:1556px"><span class="dot">•</span>Permanente Make Up</li>
    <li class="service" style="top:1726px"><span class="dot">•</span>Airbrush Tanning</li>
    <li class="service" style="top:1896px"><span class="dot">•</span>Manicure<span class="sep">•</span>Pedicure<span class="sep">•</span>Nalkyn</li>
  </ul>

  <section class="appointment">
    <div class="appointment-art" role="img" aria-label="Waterverf-illustratie van een oog met wimpers in blauw, geel en paars"></div>
    <div class="appointment-text">
      <p class="appointment-note">Enkel op afspraak</p>
      <p class="appointment-call">Bel 0486391524</p>
    </div>
  </section>

  <p class="website">www.zaalmira.be</p>
</main>
</body>
</html>
```